We are a recruitment company based in Norwich/Cambridge England.
I have included our company logo which we want to remain the same.

What we are looking for is a new creative Business card which will really stand out!!

Contact Information for Business Card

Harriet Dunmore
email: Harriet@plavex.co.uk
Address: Brackwell House
Fenmoor Enterprise Park
Partridge Way
Norwich
QB9 3KX
Tel:01632 960418

```html
<!DOCTYPE html>
<html lang="en">
<head>
<meta charset="utf-8">
<title>Plavex Business Card</title>
<link rel="stylesheet" href="https://fonts.googleapis.com/css2?family=Open+Sans:wght@400;600;700&display=swap">
<style>
  :root {
    --backdrop: #3a3a3c;
    --card-grey: #9a9196;
    --brand-green: #9fd10f;
    --brand-green-light: #b6e02f;
    --paper: #ffffff;
    --logo-grey: #8c8589;
    --ink-light: #ecebec;
  }
  html, body {
    margin: 0;
    padding: 0;
    width: 1200px;
    height: 900px;
    overflow: hidden;
    background: var(--backdrop);
    font-family: "Open Sans", Arial, sans-serif;
  }
  .canvas {
    position: relative;
    width: 1200px;
    height: 900px;
  }
  .card {
    position: absolute;
    width: 560px;
    height: 320px;
    border-radius: 18px;
    overflow: hidden;
    box-shadow: 0 10px 30px rgba(0,0,0,0.45);
  }
  .card--front { left: 70px; top: 90px; }
  .card--back {
    left: 570px; top: 490px;
    background: var(--card-grey);
    display: flex;
    align-items: center;
    justify-content: center;
  }
  .card svg { display: block; }
  .brand-mark {
    display: flex;
    align-items: center;
    gap: 14px;
  }
  .brand-mark__dot {
    width: 58px;
    height: 58px;
    border-radius: 50%;
    background: var(--paper);
  }
  .brand-mark__name {
    font-weight: 700;
    font-size: 62px;
    color: var(--paper);
    letter-spacing: -1px;
    line-height: 1;
  }
</style>
</head>
<body>
<main class="canvas">

  <section class="card card--front" aria-label="Business card front">
    <svg width="560" height="320" viewBox="0 0 560 320">
      <defs>
        <linearGradient id="steel-stripe" x1="0" y1="0" x2="1" y2="0">
          <stop offset="0" stop-color="#1b1b1b"/>
          <stop offset="0.5" stop-color="#5a5a5a"/>
          <stop offset="1" stop-color="#e8e8e8"/>
        </linearGradient>
      </defs>
      <rect class="front-base" width="560" height="320" fill="var(--card-grey)"/>
      <path class="front-paper" d="M0 0 H560 V80 C420 150 250 190 0 205 Z" fill="var(--paper)"/>
      <path class="front-swoosh" d="M0 205 C250 190 420 150 560 80 V112 C420 178 250 218 0 242 Z" fill="var(--brand-green)"/>
      <path class="front-swoosh-glow" d="M0 222 C250 206 420 164 560 96 V104 C420 172 250 212 0 230 Z" fill="var(--brand-green-light)" opacity="0.6"/>
      <path class="front-steel" d="M560 84 C460 126 390 196 300 320 H330 C400 200 470 130 560 92 Z" fill="url(#steel-stripe)"/>
      <path class="front-panel" d="M560 92 C470 130 400 200 330 320 H560 Z" fill="var(--brand-green)"/>

      <g class="front-logo">
        <circle cx="268" cy="56" r="22" fill="var(--logo-grey)"/>
        <text x="300" y="72" font-family="Open Sans, Arial, sans-serif" font-weight="700" font-size="44" fill="var(--brand-green)">Plavex</text>
      </g>

      <g class="front-contact" font-family="Open Sans, Arial, sans-serif" font-size="14" fill="var(--paper)" text-anchor="end">
        <text x="526" y="150">01632 960418</text>
        <text x="526" y="172">Harriet@plavex.co.uk</text>
        <text x="526" y="194">www.plavex.co.uk</text>
        <text x="540" y="216">Fenmoor Enterprise Park</text>
        <text x="540" y="238">Partridge Way Norwich QB9 3KX</text>
      </g>

      <g class="front-icons" fill="none" stroke="var(--paper)" stroke-width="1.4">
        <circle cx="540" cy="145" r="6"/>
        <path d="M537 142 q0 5 5 7" />
        <rect x="534" y="163" width="12" height="8" rx="1"/>
        <path d="M534 163 l6 5 l6 -5"/>
        <circle cx="540" cy="189" r="6"/>
        <path d="M534 189 h12 M540 183 v12"/>
      </g>

      <g class="front-person" font-family="Open Sans, Arial, sans-serif">
        <text x="36" y="262" font-weight="700" font-size="20" fill="var(--paper)">HARRIET DUNMORE</text>
        <text x="46" y="284" font-size="15" fill="var(--ink-light)">President</text>
      </g>
    </svg>
  </section>

  <section class="card card--back" aria-label="Business card back">
    <div class="brand-mark">
      <span class="brand-mark__dot"></span>
      <span class="brand-mark__name">Plavex</span>
    </div>
  </section>

</main>
</body>
</html>
```